Structural Engineering Business Card

Brookvane Drafting does residential house plans for clients in Central Florida. Would like simple but elegant business card that is appropriate for a house plan engineering company. Prefer black business card with black/white them but open to other shades of blue. I uploaded a sample card that I came across that looked good but please come up with your own creative designs.

Contact Information for Business Card

Name, Title, Phone, Email, Address, website

```html
<!DOCTYPE html>
<html lang="en">
<head>
<meta charset="utf-8">
<title>Brookvane Drafting — Business Card</title>
<link href="https://fonts.googleapis.com/css2?family=Montserrat:wght@800&family=Arimo:wght@400;700&display=swap" rel="stylesheet">
<style>
  :root {
    --stage: #1c1c1c;
    --ink: #000000;
    --paper: #ffffff;
    --rule: #555555;
  }
  * { margin: 0; padding: 0; box-sizing: border-box; }
  html, body { width: 1200px; height: 1015px; overflow: hidden; }
  body {
    background: var(--stage);
    display: flex;
    flex-direction: column;
    align-items: center;
    justify-content: center;
    gap: 64px;
    font-family: "Arimo", Arial, sans-serif;
  }
  .card {
    width: 640px;
    height: 366px;
    position: relative;
    overflow: hidden;
  }
  .card--front { background: var(--ink); }
  .card--back { background: var(--paper); color: var(--ink); }

  .brand-name {
    font-family: "Montserrat", Arial, sans-serif;
    font-weight: 800;
    text-transform: uppercase;
    letter-spacing: 0.5px;
    line-height: 1;
  }
  .card--front .brand-name {
    position: absolute;
    left: 0; right: 0;
    top: 112px;
    text-align: center;
    font-size: 44px;
    color: var(--paper);
  }
  .card--front .web-band {
    position: absolute;
    left: 0; right: 0;
    top: 232px;
    height: 72px;
    background: var(--paper);
    display: flex;
    align-items: flex-start;
    justify-content: center;
  }
  .web-band .web-url {
    margin-top: -34px;
    color: var(--paper);
    font-size: 17px;
    letter-spacing: 0.6px;
  }

  .card--back .brand-block {
    position: absolute;
    left: 40px;
    top: 0; bottom: 0;
    width: 258px;
    display: flex;
    align-items: center;
  }
  .card--back .brand-name { font-size: 25px; line-height: 1.15; }
  .card--back .divider {
    position: absolute;
    left: 318px;
    top: 110px;
    width: 1px;
    height: 150px;
    background: var(--rule);
  }
  .contact {
    position: absolute;
    left: 342px;
    top: 96px;
    font-size: 16px;
    line-height: 1.2;
  }
  .contact .person-name { font-weight: 700; font-size: 21px; letter-spacing: 0.6px; }
  .contact .person-title { font-size: 15px; margin-bottom: 12px; }
  .contact-list { list-style: none; margin-bottom: 12px; }
  .contact-list li { display: flex; align-items: center; gap: 7px; margin-bottom: 2px; }
  .contact-list svg { width: 14px; height: 14px; flex: none; }
  .address { font-size: 16px; line-height: 1.2; }
</style>
</head>
<body>

  <section class="card card--front" aria-label="Card front">
    <div class="brand-name">Brookvane Drafting</div>
    <div class="web-band"><span class="web-url">www.brookvanedrafting.com</span></div>
  </section>

  <section class="card card--back" aria-label="Card back">
    <div class="brand-block"><div class="brand-name">Brookvane<br>Drafting</div></div>
    <div class="divider"></div>
    <div class="contact">
      <div class="person-name">DANIEL MERCER</div>
      <div class="person-title">Managing Director</div>
      <ul class="contact-list">
        <li>
          <svg viewBox="0 0 16 16" aria-hidden="true"><circle cx="8" cy="8" r="7.5" fill="var(--ink)"/><path d="M5.2 4.2l1.4 1.6-.8 1c.5 1.1 1.3 1.9 2.4 2.4l1-.8 1.6 1.4-.9 1.2C7.4 10.8 5.2 8.6 4 5.1z" fill="var(--paper)"/></svg>
          <span>044-321 654 987</span>
        </li>
        <li>
          <svg viewBox="0 0 16 16" aria-hidden="true"><rect x="1" y="3.5" width="14" height="9" fill="var(--ink)"/><path d="M1 3.5l7 5 7-5" fill="none" stroke="var(--paper)" stroke-width="1.2"/></svg>
          <span>info@brookvane.com</span>
        </li>
        <li>
          <svg viewBox="0 0 16 16" aria-hidden="true"><circle cx="8" cy="8" r="7.5" fill="var(--ink)"/><g fill="none" stroke="var(--paper)" stroke-width="0.9"><ellipse cx="8" cy="8" rx="3" ry="6"/><path d="M2 8h12M3 5h10M3 11h10"/></g></svg>
          <span>www.brookvanedrafting.com</span>
        </li>
      </ul>
      <div class="address">421, Address line goes here<br>45452, Country Name</div>
    </div>
  </section>

</body>
</html>
```